Residential Remodeling Contractor needs updated business card

I need a new design for my business card.
Name of the company is Ridgefell Construction. I need a card that commands presence, strength, integrity. I have been in business for 28 years. I am a Residential Remodeling Contractor that covers all aspects of a residential remodel and build.

```html
<!DOCTYPE html>
<html lang="en">
<head>
<meta charset="utf-8">
<title>Ridgefell Construction – Business Card</title>
<link rel="stylesheet" href="https://fonts.googleapis.com/css2?family=Open+Sans:wght@400;600;700&display=swap">
<style>
  :root {
    --backdrop: #232323;
    --navy: #223f80;
    --navy-deep: #1b3570;
    --navy-ink: #203c7c;
    --paper: #ffffff;
    --swoosh-light: #c9cde6;
  }
  html, body {
    margin: 0;
    padding: 0;
    width: 1200px;
    height: 780px;
    overflow: hidden;
    background: var(--backdrop);
  }
  .canvas {
    position: relative;
    width: 1200px;
    height: 780px;
    display: flex;
    align-items: center;
    justify-content: center;
    gap: 40px;
    font-family: "Open Sans", Arial, sans-serif;
  }
  .card {
    position: relative;
    width: 540px;
    height: 310px;
    border-radius: 2px;
    overflow: hidden;
    box-shadow: 0 14px 30px rgba(0,0,0,0.55);
  }
  .card-front { background: var(--paper); color: var(--navy-ink); }
  .card-back { background: var(--navy); display: flex; align-items: center; justify-content: center; }

  .front-band { position: absolute; inset: 0; }

  .company-name {
    position: absolute;
    top: 58px;
    left: 262px;
    margin: 0;
    font-weight: 600;
    font-size: 27px;
    line-height: 1.08;
    letter-spacing: 0.02em;
    color: var(--navy-ink);
    text-transform: uppercase;
  }
  .person {
    position: absolute;
    top: 36px;
    left: 34px;
  }
  .person-name {
    margin: 0;
    font-weight: 700;
    font-size: 23px;
    line-height: 1.1;
  }
  .person-title {
    margin: 2px 0 0 26px;
    font-size: 13px;
  }
  .divider {
    position: absolute;
    left: 238px;
    top: 136px;
    width: 2px;
    height: 72px;
    background: var(--navy-ink);
  }
  .contact-list {
    position: absolute;
    left: 254px;
    top: 140px;
    margin: 0;
    padding: 0;
    list-style: none;
    font-size: 14px;
    line-height: 22px;
  }
  .contact-list li { display: flex; align-items: center; gap: 8px; }
  .contact-list svg { width: 13px; height: 13px; flex: none; }
  .address {
    position: absolute;
    left: 30px;
    bottom: 14px;
    margin: 0;
    font-size: 13px;
    color: var(--paper);
    letter-spacing: 0.01em;
  }
  .back-name {
    margin: 0;
    font-weight: 600;
    font-size: 38px;
    line-height: 1.1;
    letter-spacing: 0.03em;
    text-transform: uppercase;
    color: #2f4f96;
    text-align: center;
  }
</style>
</head>
<body>
<main class="canvas">
  <section class="card card-front" aria-label="Card front">
    <svg class="front-band" viewBox="0 0 540 310" preserveAspectRatio="none" aria-hidden="true">
      <defs>
        <linearGradient id="swoosh-line" x1="0" y1="0" x2="1" y2="0">
          <stop offset="0" stop-color="#223f80"/>
          <stop offset="0.55" stop-color="#ffffff"/>
          <stop offset="1" stop-color="#223f80"/>
        </linearGradient>
      </defs>
      <path d="M0,190 Q250,292 540,292 L540,310 L0,310 Z" fill="var(--navy)"/>
      <path d="M18,170 Q250,282 520,280" fill="none" stroke="url(#swoosh-line)" stroke-width="3"/>
    </svg>

    <h1 class="company-name">Ridgefell<br>Construction</h1>

    <div class="person">
      <p class="person-name">Marisol Deverin</p>
      <p class="person-title">Managing Director</p>
    </div>

    <div class="divider"></div>

    <ul class="contact-list">
      <li>
        <svg viewBox="0 0 16 16" aria-hidden="true"><path d="M4 1l3 3-2 2c1 2 3 4 5 5l2-2 3 3-2 3C7 14 2 9 1 3z" fill="currentColor"/></svg>
        (555) 014-2283
      </li>
      <li>
        <svg viewBox="0 0 16 16" aria-hidden="true"><rect x="1" y="3" width="14" height="10" fill="none" stroke="currentColor" stroke-width="1.6"/><path d="M1 3l7 6 7-6" fill="none" stroke="currentColor" stroke-width="1.6"/></svg>
        hello@ridgefellbuild.com
      </li>
      <li>
        <svg viewBox="0 0 16 16" aria-hidden="true"><circle cx="8" cy="8" r="6.5" fill="none" stroke="currentColor" stroke-width="1.5"/><path d="M1.5 8h13M8 1.5c-3 3.5-3 9.5 0 13M8 1.5c3 3.5 3 9.5 0 13" fill="none" stroke="currentColor" stroke-width="1.2"/></svg>
        www.ridgefellbuild.com
      </li>
    </ul>

    <p class="address">740 Harlow Ave. Suite 310 Alder Springs, TX 75021</p>
  </section>

  <section class="card card-back" aria-label="Card back">
    <p class="back-name">Ridgefell<br>Construction</p>
  </section>
</main>
</body>
</html>
```